Fizz's Shed & Grill Burger Restaurant Website - HomePage Only PSD

I need a website design for a restaurant called "Fizz's Shed and Grill" featuring burgers, wings, beer, live music, trivia, and more. I have several images of the restaurant and they already have their logo files created (see attached). I want some type of wood background and integrate the silver tin. This needs to be a modern, hip and fun type design. Design must incorporate these attached graphics.

UPDATE - just added a few more images of things I really like to be incorporated into my designs.
Updates

Industry/Entity Type

Burger Restaurant

Number of Pages Required

1 page

Font styles to use
Sans Serif

Requirements
Must have
• Restaurant/Bar theme with integration of existing logo and the red wood look.
Nice to have
• - Modern Fun appearance
• - Use Pelko Fonts

```html
<!DOCTYPE html>
<html lang="en">
<head>
<meta charset="utf-8">
<title>Fizz's Shed and Grill</title>
<link rel="stylesheet" href="https://fonts.googleapis.com/css2?family=Open+Sans:wght@300;400;600&display=swap">
<style>
  :root {
    --wood-light: #c98c52;
    --wood-mid: #b0713b;
    --wood-dark: #8a5328;
    --page: #f6f6f6;
    --white: #ffffff;
    --ink: #1e1e1e;
    --text-soft: #6d6d6d;
    --nav: #7a7a7a;
    --nav-active: #6b3f1f;
    --brown: #6b3f1f;
    --rule: #dcdcdc;
    --tile-label: #3b3b3b;
    --quote: #9a9a9a;
    --dot: #9b9b9b;
    --dot-active: #1f6fb8;
    --tin-light: #e4e8ee;
    --tin-dark: #a9b1bc;
    --social: #8a8a8a;
  }
  * { box-sizing: border-box; margin: 0; padding: 0; }
  html, body { width: 1143px; height: 1200px; overflow: hidden; }
  body {
    position: relative;
    font-family: "Open Sans", sans-serif;
    background: linear-gradient(180deg, var(--wood-light) 0%, var(--wood-mid) 45%, var(--wood-light) 70%, var(--wood-dark) 100%);
  }
  .page {
    position: absolute; left: 125px; top: 46px; width: 891px; height: 1154px;
    background: var(--page);
  }
  .site-header {
    position: absolute; left: 0; top: 0; width: 891px; height: 38px;
    background: var(--white);
    display: flex; align-items: center;
  }
  .main-nav { display: flex; gap: 0; margin-left: 27px; }
  .main-nav a {
    font-size: 11.5px; color: var(--nav); text-decoration: none; margin-right: 33px;
  }
  .main-nav a.is-active { color: var(--nav-active); }
  .call-us {
    position: absolute; left: 592px; top: 11px;
    font-size: 12.5px; color: var(--brown); display: flex; align-items: center; gap: 5px;
  }
  .social {
    position: absolute; left: 786px; top: 13px; display: flex; gap: 16px;
  }
  .social span { width: 11px; height: 11px; border-radius: 50%; background: var(--social); display: block; }
  .brand-badge {
    position: absolute; left: 388px; top: -40px; width: 118px; height: 118px;
    border-radius: 50%; background: var(--white); border: 3px solid var(--ink);
    display: flex; align-items: center; justify-content: center; text-align: center;
    font-size: 14px; font-weight: 600; color: var(--ink); line-height: 1.2; z-index: 3;
    padding: 14px;
  }
  .hero {
    position: absolute; left: 0; top: 38px; width: 891px; height: 347px;
    background: linear-gradient(180deg, #c46a63 0%, #b45a50 9%, #d9d6cf 22%, #cfcac2 55%, #6f7450 80%, #5a5c40 100%);
  }
  .hero-dots {
    position: absolute; left: 0; right: 0; top: 397px; display: flex; justify-content: center; gap: 8px;
  }
  .hero-dots span { width: 8px; height: 8px; border-radius: 50%; border: 1.5px solid var(--white); display: block; }
  .hero-dots span.is-active { background: transparent; }
  .welcome { position: absolute; left: 25px; width: 841px; top: 413px; text-align: center; }
  .welcome h1 { font-weight: 400; font-size: 24px; color: var(--ink); }
  .welcome p { margin-top: 10px; font-size: 9.6px; line-height: 18px; color: var(--text-soft); }
  .rule { position: absolute; left: 8px; width: 875px; height: 1px; background: var(--rule); }
  .about-title {
    position: absolute; top: 553px; left: 0; width: 891px; text-align: center;
    font-weight: 300; font-size: 24px; color: var(--ink);
  }
  .features { position: absolute; left: 12px; top: 594px; display: flex; gap: 5px; }
  .feature { width: 170px; }
  .feature-photo { height: 153px; display: block; }
  .feature-label {
    height: 39px; background: var(--tile-label); color: var(--white);
    font-size: 16px; display: flex; align-items: center; justify-content: center;
  }
  .and-more { position: absolute; top: 814px; width: 891px; text-align: center; font-size: 15px; color: var(--ink); }
  .testimonial { position: absolute; top: 880px; left: 40px; width: 811px; text-align: center; }
  .testimonial blockquote {
    font-weight: 300; font-size: 27px; line-height: 38px; color: var(--quote);
  }
  .testimonial .mark { font-weight: 600; color: #777; font-size: 34px; vertical-align: -6px; }
  .testimonial cite { display: block; margin-top: 12px; font-style: normal; font-size: 16px; color: var(--ink); }
  .quote-dots { position: absolute; top: 1018px; left: 0; width: 891px; display: flex; justify-content: center; gap: 11px; }
  .quote-dots span { width: 12px; height: 12px; border-radius: 50%; background: var(--dot); display: block; }
  .quote-dots span.is-active { background: var(--dot-active); }
  .site-footer {
    position: absolute; left: 0; top: 1063px; width: 891px; height: 91px;
    background: linear-gradient(180deg, var(--tin-light), #cdd3db 60%, var(--tin-dark));
    text-align: center; color: var(--ink); font-size: 11.5px;
  }
  .footer-nav { margin-top: 32px; }
  .footer-nav a { color: var(--ink); text-decoration: none; }
  .footer-nav .sep { margin: 0 8px; }
  .copyright { margin-top: 10px; }
</style>
</head>
<body>
  <div class="page">
    <header class="site-header">
      <nav class="main-nav">
        <a href="#" class="is-active">Home</a>
        <a href="#">Menu</a>
        <a href="#">Drinks</a>
        <a href="#">Book a Table</a>
        <a href="#">Location</a>
      </nav>
      <div class="brand-badge">Fizz's Shed and Grill</div>
      <div class="call-us">
        <svg width="11" height="11" viewBox="0 0 24 24" aria-hidden="true"><path fill="currentColor" d="M6.6 10.8a15.1 15.1 0 0 0 6.6 6.6l2.2-2.2a1 1 0 0 1 1-.25 11.4 11.4 0 0 0 3.6.57 1 1 0 0 1 1 1V20a1 1 0 0 1-1 1A17 17 0 0 1 3 4a1 1 0 0 1 1-1h3.5a1 1 0 0 1 1 1c0 1.25.2 2.45.57 3.57a1 1 0 0 1-.25 1z"/></svg>
        Call us on : 555 010 2476
      </div>
      <div class="social" aria-label="Social links"><span></span><span></span><span></span><span></span></div>
    </header>

    <div class="hero" role="img" aria-label="Photo of the restaurant front: brick building with red tin roof and a longhorn statue in front"></div>
    <div class="hero-dots"><span class="is-active"></span><span></span><span></span><span></span></div>

    <section class="welcome">
      <h1>Welcome to Fizz's Shed and Grill</h1>
      <p>Aliquam eu odio et sem maximus eleifend. In ut tincidunt neque, vel vestibulum ligula. Sed nibh magna, blandit eget venenatis sit amet, lobortis et erat. Vestibulum aliquam, tellus quis volutpat consequat, lacus libero ullamcorper nisi, nec congue elit urna id augue. Curabitur volutpat commodo nulla quis finibus. Etiam quis quam sit amet ipsum consequat pharetra vitae sed velit. Proin vitae dapibus lorem, at scelerisque nisi. Donec ultrices velit ac tellus sagittis, fermentum hendrerit justo egestas.</p>
    </section>

    <div class="rule" style="top:531px"></div>
    <h2 class="about-title">Our restaurant is about...</h2>

    <div class="features">
      <div class="feature"><div class="feature-photo" role="img" aria-label="Photo of burgers" style="background:linear-gradient(160deg,#6b5a4a,#8a6a3a 50%,#4a5a2a)"></div><div class="feature-label">Burgers</div></div>
      <div class="feature"><div class="feature-photo" role="img" aria-label="Photo of chicken wings" style="background:linear-gradient(160deg,#c07a3a,#8a3a1a 55%,#e0d0c0)"></div><div class="feature-label">Wings</div></div>
      <div class="feature"><div class="feature-photo" role="img" aria-label="Photo of a glass of beer" style="background:linear-gradient(90deg,#3a2a1e,#d9a03a 40%,#4a3020)"></div><div class="feature-label">Beer</div></div>
      <div class="feature"><div class="feature-photo" role="img" aria-label="Photo of a band playing live music" style="background:linear-gradient(160deg,#5a2a1a,#a0603a 45%,#1e1410)"></div><div class="feature-label">Live Music</div></div>
      <div class="feature"><div class="feature-photo" role="img" aria-label="Photo of letter tiles spelling trivia" style="background:linear-gradient(160deg,#5a5a5a,#c8b898 50%,#4a4a4a)"></div><div class="feature-label">Trivia</div></div>
    </div>

    <p class="and-more">and more...</p>
    <div class="rule" style="top:854px"></div>

    <section class="testimonial">
      <blockquote><span class="mark">&ldquo;</span> Praesent porta tortor dolor, quis maximus tortor pretium et. Praesent eget vulputate risus. Suspendisse dignissim. <span class="mark">&rdquo;</span></blockquote>
      <cite>- Dana Hurst, City name</cite>
    </section>
    <div class="quote-dots"><span class="is-active"></span><span></span><span></span><span></span></div>

    <footer class="site-footer">
      <nav class="footer-nav">
        <a href="#">Home</a><span class="sep">|</span><a href="#">Menu</a><span class="sep">|</span><a href="#">Drinks</a><span class="sep">|</span><a href="#">Book a Table</a><span class="sep">|</span><a href="#">Location</a>
      </nav>
      <p class="copyright">Copyright &copy; 2016 &nbsp;Fizz's Shed and Grill. &nbsp;All rights reserved.</p>
    </footer>
  </div>
</body>
</html>
```